Website for Reiki and Wellness Courses

I teach online courses in Reiki and wellness/self-development and am needing a new website.

The focus of the website will be to provide descriptions of the courses as well as include a blog and pages where students in my courses will visit for additional information.

Note: courses are NOT hosted on this site.
The focus of this website will be to encourage viewers to enroll in courses as well as opt in to the email list.

I will upload copy soon. My old website is: http://brightfernstudies.example. Please do not use existing logo.

Target Market(s)

Alternative health, wellness, spirituality, personal development. Males and females of all ages seeking to improve their health and life.

Industry/Entity Type

Health And Wellness

Logo Text

No text (please do not use existing logo)

Coding

Coded - Design and coding required

Number of Pages Required

5+ page

Requirements
Must have
• 1. Home page
• 2. About page
• 3. Courses page that outlines courses (there are currently 6 courses with 1 coming soon)
• 4. Individual course page (maybe a template that I can adjust color and pictures for with each course)
• 5. Blog
• 6. Student Area that outlines all Student Areas
• 7. Individual Student Area page (maybe a template that I can adjust color and pictures for with each course)
• 8. Shop page (note: items will not currently be purchased through website - it will be a link to quillmarket for a book).
• 9. Student thank-you page (maybe a template that I can adjust color and pictures for with each course) this is the page students are directed to at end of course with vouchers for other courses.
• Opt-in for the home page, course pages, blog and thank-you pages
Nice to have
• I would like the design to be calm, clean and soothing. Ideally visitors feel relaxed when viewing the site and are encouraged to explore the courses, subscribe to the email list and purchase a product.
• ~ Testimonials page
• ~ Contact page
• I tend to gravitate towards blues, greys and purples as well as monochromatic color schemes.
Should not have
• Contact form on home page
• phone number on home page
• location/physical address
• dates for blog posts

```html
<!DOCTYPE html>
<html lang="en">
<head>
<meta charset="utf-8">
<title>Bright Fern Studies — Reiki and Wellness</title>
<link href="https://fonts.googleapis.com/css2?family=Oswald:wght@500&family=Roboto+Slab:wght@300;400;700&family=Roboto:wght@400;500;700&display=swap" rel="stylesheet">
<style>
:root{
  --ink:#2b2b2b;
  --text:#666a70;
  --slate:#6f7492;
  --slate-dark:#5d617c;
  --button:#565b74;
  --heading-blue:#565b74;
  --light:#ececec;
  --footer:#1b1b1b;
  --footer-deep:#0e0e0e;
  --footer-line:#3a3a3a;
  --white:#ffffff;
}
*{box-sizing:border-box;margin:0;padding:0}
html,body{width:1200px;height:2757px;overflow:hidden;background:var(--white)}
body{position:relative;font-family:"Roboto Slab",serif;color:var(--text)}

/* header */
.site-header{position:absolute;left:0;top:0;width:1200px;height:101px;background:var(--white)}
.brand{position:absolute;left:105px;top:22px;display:flex;align-items:center;gap:12px}
.brand-mark{width:52px;height:52px;border-radius:50%;background:var(--slate)}
.brand-name{font-family:"Roboto",sans-serif;font-weight:400;font-size:23px;color:var(--slate-dark)}
.main-nav{position:absolute;right:100px;top:60px;display:flex;gap:48px;font-size:13px;color:#444}
.main-nav a{color:inherit;text-decoration:none}
.main-nav a.active{color:var(--slate)}

/* hero */
.hero{position:absolute;left:0;top:101px;width:1200px;height:600px;overflow:hidden}
.hero-photo{position:absolute;inset:0;background:linear-gradient(115deg,#c8a58e 0%,#e9d8c9 35%,#f4ece4 55%,#d8b8a0 75%,#e7e3da 100%)}
.hero-title{position:absolute;left:0;width:100%;top:362px;text-align:center;font-family:"Oswald",sans-serif;font-weight:500;font-size:42px;color:#161616;letter-spacing:.2px}
.hero-dots{position:absolute;top:493px;left:0;width:100%;display:flex;justify-content:center;gap:12px}
.hero-dots span{width:12px;height:12px;border-radius:50%;background:rgba(255,255,255,.6)}
.hero-dots span.on{background:#fff;box-shadow:0 0 0 2px #555 inset}
.hero-wave{position:absolute;left:0;bottom:0;width:1200px;height:80px}

/* welcome */
.welcome h1{position:absolute;left:100px;top:704px;font-weight:700;font-size:26px;color:var(--ink)}
.welcome-text{position:absolute;left:100px;top:756px;width:695px;font-weight:300;font-size:12.4px;line-height:21px;color:#555}
.welcome-text p{margin-bottom:14px}
.btn{display:inline-block;background:var(--button);color:#fff;font-size:12.5px;text-transform:uppercase;text-align:center;box-shadow:0 2px 0 #3d4156}
.welcome .btn{position:absolute;left:100px;top:960px;width:117px;height:40px;line-height:40px}
.welcome-photo{position:absolute;left:818px;top:716px;width:282px;height:282px;border-radius:50%;background:#eee;border:8px solid #f1f1f1;box-shadow:0 0 0 1px #ddd}
.welcome-photo div{width:100%;height:100%;border-radius:50%;background:linear-gradient(160deg,#cfd9c2 0%,#efe1d6 50%,#b99886 100%)}

/* certification band */
.cert{position:absolute;left:0;top:1048px;width:1200px;height:594px;background:var(--slate)}
.cert h2{position:absolute;top:42px;width:100%;text-align:center;color:#fff;font-weight:700;font-size:24px}
.cert .lead{position:absolute;top:78px;left:350px;width:500px;text-align:center;color:#fff;font-size:14px;line-height:21px}
.card{position:absolute;top:150px;width:322px;height:381px;background:#fff}
.card-photo{position:relative;height:210px;overflow:hidden}
.card-photo svg{position:absolute;left:0;bottom:-1px;width:100%;height:40px}
.card h3{margin-top:6px;text-align:center;font-weight:700;font-size:14px;color:var(--ink);line-height:18px;padding:0 40px;min-height:36px;display:flex;align-items:center;justify-content:center}
.card p{margin-top:10px;text-align:center;font-weight:300;font-size:12px;line-height:20px;color:#555;padding:0 30px}
.card a{display:block;margin-top:14px;text-align:center;font-size:12px;color:#888;text-decoration:underline;text-transform:uppercase}

/* courses */
.courses h2{position:absolute;left:100px;top:1694px;font-weight:700;font-size:24px;color:var(--ink)}
.course{position:absolute;left:100px;width:510px}
.course h3{font-weight:700;font-size:14.5px;color:var(--heading-blue);text-transform:uppercase}
.course p{margin-top:8px;font-weight:300;font-size:11.5px;line-height:19px;color:#555}

.optin{position:absolute;left:781px;top:1704px;width:320px;height:375px;border:1px solid #d8d8d8;background:#f7f7f7}
.optin-head{height:62px;background:var(--slate);color:#fff;font-weight:700;font-size:17px;text-align:center;line-height:62px;text-transform:uppercase}
.field{margin:24px 0 0 21px;width:277px;height:46px;border:1px solid #cfcfcf;background:#fff;font-size:11px;color:#999;line-height:44px;padding-left:18px}
.field + .field{margin-top:26px}
.optin .go{display:block;margin:22px auto 0;width:190px;height:44px;line-height:44px;background:#2f2f2f;color:#fff;font-weight:700;font-size:13.5px;text-align:center;text-transform:uppercase}

/* testimonials */
.results{position:absolute;left:0;top:2132px;width:1200px;height:257px;background:var(--light)}
.results h2{position:absolute;top:34px;width:100%;text-align:center;font-weight:700;font-size:25px;color:var(--ink)}
.quote{position:absolute;top:105px;width:520px;height:100px}
.quote-photo{position:absolute;left:0;top:0;width:100px;height:97px;border:3px solid #fff;background:linear-gradient(150deg,#b9aa9d,#6b5b50);box-shadow:0 0 0 1px #ccc}
.quote-open{position:absolute;left:110px;top:-6px;font-size:40px;color:#555;line-height:1}
.quote-body{position:absolute;left:135px;top:6px;width:340px;font-weight:300;font-size:11.5px;line-height:18px;color:#777}
.quote-foot{position:absolute;left:135px;top:76px;width:340px;display:flex;justify-content:center;align-items:flex-start;gap:18px}
.quote-name{margin-top:10px;font-weight:700;font-size:13.5px;color:#555}
.quote-close{font-size:40px;color:#555;line-height:1}

/* footer */
.site-footer{position:absolute;left:0;top:2389px;width:1200px;height:368px;background:var(--footer);font-family:"Roboto",sans-serif}
.fcol{position:absolute;top:40px}
.fcol h4{font-size:17px;font-weight:500;color:#fff;text-transform:uppercase;margin-bottom:10px;padding-bottom:14px;position:relative}
.fcol h4::after{content:"";position:absolute;left:0;bottom:0;width:30px;height:2px;background:#fff}
.fcol ul{list-style:none;width:150px}
.fcol li{font-size:11.5px;color:#ddd;text-transform:uppercase;padding:10px 0;border-bottom:1px solid var(--footer-line)}
.fcol li:last-child{border-bottom:0}
.contact ul{width:200px}
.contact li{text-transform:none}
.contact li u{color:#ddd}
.news p{font-size:11.5px;line-height:18px;color:#ddd;width:300px;margin-top:4px}
.news-input{margin-top:12px;width:295px;height:44px;background:#2e2e2e;position:relative;font-size:11.5px;color:#ccc;line-height:44px;padding-left:14px}
.news-input span{position:absolute;right:0;top:0;width:45px;height:44px;background:var(--slate)}
.socials{display:flex;gap:12px;margin-top:20px}
.socials i{width:30px;height:30px;border-radius:50%;background:#3b5b9a;border:2px solid #fff}
.socials i:nth-child(2){background:#3ba3d9}
.socials i:nth-child(3){background:#d34836}
.footer-bar{position:absolute;left:0;top:303px;width:1200px;height:65px}
.footer-bar .copy{position:absolute;left:100px;top:26px;font-size:12px;color:#ccc}
.footer-bar nav{position:absolute;right:28px;top:26px;display:flex;gap:36px;font-size:12.5px;color:#ddd}
.footer-bar svg{position:absolute;left:0;top:0}
</style>
</head>
<body>

<header class="site-header">
  <div class="brand"><span class="brand-mark"></span><span class="brand-name">Bright Fern Studies</span></div>
  <nav class="main-nav">
    <a class="active">HOME</a><a>ABOUT</a><a>COURSES</a><a>BLOG</a><a>STUDENT AREAS</a><a>CONTACT</a>
  </nav>
</header>

<section class="hero">
  <div class="hero-photo" role="img" aria-label="Photo of a practitioner's hand held above a client's feet during a Reiki session"></div>
  <h2 class="hero-title">REIKI AND WELLNESS/SELF-DEVELOPMENT</h2>
  <div class="hero-dots"><span></span><span class="on"></span><span></span><span></span></div>
  <svg class="hero-wave" viewBox="0 0 1200 80" preserveAspectRatio="none"><path fill="#fff" d="M0 80 L0 50 Q600 -30 1200 50 L1200 80 Z"/></svg>
</section>

<section class="welcome">
  <h1>WELCOME !</h1>
  <div class="welcome-text">
    <p>Thought to be centuries old and rediscovered in the late 1800's, Reiki (pronounced ray-key) is a healing and enlightenment system. Reiki can be translated into "Universal (Rei) Life Energy (Ki)". As a practitioner of Reiki, you attune your awareness to this energy and utilize it for the physical and emotional healing of self and others.</p>
    <p>Reiki is non-denominational and can be practiced by everyone, regardless of their religious and spiritual beliefs. Reiki can be performed hands-on in person or from a distance.</p>
    <p>Have you ever seen a mother kiss a child's elbow after they fall? What is your response when you stub your toe or bang your shin? We instinctively touch and focus on areas in pain or need. Reiki is an extension of this innate wisdom.</p>
  </div>
  <a class="btn">Learn More</a>
  <div class="welcome-photo"><div role="img" aria-label="Photo of a woman relaxing during a Reiki treatment"></div></div>
</section>

<section class="cert">
  <h2>BECOME A CERTIFIED USUI REIKI MASTER</h2>
  <p class="lead">This comprehensive online course gives you all of the tools you need to be certified as a Traditional Usui Reiki Master.</p>

  <article class="card" style="left:99px">
    <div class="card-photo"><div role="img" aria-label="Photo of a woman receiving a head treatment" style="height:100%;background:linear-gradient(160deg,#f1ece6,#d8c1b0 60%,#f4f4f2)"></div>
      <svg viewBox="0 0 322 40" preserveAspectRatio="none"><path fill="#fff" d="M0 40 L0 18 Q161 -12 322 18 L322 40 Z"/></svg></div>
    <h3>HOW REIKI WORKS</h3>
    <p>Reiki has been used for centuries to help individuals with physical and emotional imbalances as well as those seeking clarity and.</p>
    <a>Learn More</a>
  </article>

  <article class="card" style="left:439px">
    <div class="card-photo"><div role="img" aria-label="Photo of stacked pebbles on a beach under blue sky" style="height:100%;background:linear-gradient(180deg,#7fb1d6,#c9dbe6 55%,#a9b0b5)"></div>
      <svg viewBox="0 0 322 40" preserveAspectRatio="none"><path fill="#fff" d="M0 40 L0 18 Q161 -12 322 18 L322 40 Z"/></svg></div>
    <h3>TRADITIONAL USUI REIKI MASTER CERTIFICATION</h3>
    <p>Reiki has been used for centuries to help individuals with physical and emotional imbalances as well as those seeking clarity and.</p>
    <a>Learn More</a>
  </article>

  <article class="card" style="left:779px">
    <div class="card-photo"><div role="img" aria-label="Photo of black stones reflected on water" style="height:100%;background:linear-gradient(180deg,#f2f2f2,#8f8f8f 55%,#2a2a2a)"></div>
      <svg viewBox="0 0 322 40" preserveAspectRatio="none"><path fill="#fff" d="M0 40 L0 18 Q161 -12 322 18 L322 40 Z"/></svg></div>
    <h3>RESOURCES</h3>
    <p>Reiki has been used for centuries to help individuals with physical and emotional imbalances as well as those seeking clarity and.</p>
    <a>Learn More</a>
  </article>
</section>

<section class="courses">
  <h2>ABOUT ONLINE COURSES</h2>
  <div class="course" style="top:1758px"><h3>Reiki Level I, II and Master Certification</h3><p>Learn about Reiki, a universal energy that has been used successfully all over the world to heal emotional, physical and energetic imbalances. In this course you will learn.</p></div>
  <div class="course" style="top:1846px"><h3>Animal Reiki Practitioner Certification</h3><p>Learn about Reiki, a universal energy that has been used successfully all over the world to heal emotional, physical and energetic imbalances. In this course you will learn.</p></div>
  <div class="course" style="top:1934px"><h3>Acupressure and Reiki for Anxiety and Depression</h3><p>Learn about Reiki, a universal energy that has been used successfully all over the world to heal emotional, physical and energetic imbalances. In this course you will learn.</p></div>
  <div class="course" style="top:2023px"><h3>Your Soul is Calling: Creating Your Ideal Life</h3><p>Learn about Reiki, a universal energy that has been used successfully all over the world to heal emotional, physical and energetic imbalances. In this course you will learn.</p></div>

  <aside class="optin">
    <div class="optin-head">Stay Inspired</div>
    <div class="field">First Name :</div>
    <div class="field">Last Name :</div>
    <div class="field">Email Address :</div>
    <a class="go">Yes-Count Me In</a>
  </aside>
</section>

<section class="results">
  <h2>CLIENT RESULTS</h2>
  <div class="quote" style="left:99px">
    <div class="quote-photo" role="img" aria-label="Portrait photo of a client"></div>
    <span class="quote-open">&ldquo;</span>
    <p class="quote-body">The course felt calm and clear from the first lesson. I learned to slow down, breathe and work with energy in a gentle way, and my days now feel lighter and more balanced than before.</p>
    <div class="quote-foot"><span class="quote-name">---- Mara Lind</span><span class="quote-close">&rdquo;</span></div>
  </div>
  <div class="quote" style="left:640px">
    <div class="quote-photo" role="img" aria-label="Portrait photo of a client" style="background:linear-gradient(150deg,#d2c3b5,#8a776a)"></div>
    <span class="quote-open">&ldquo;</span>
    <p class="quote-body">Each module was easy to follow and kind in tone. I finished the certification feeling confident, rested and ready to share Reiki with family and friends who need it.</p>
    <div class="quote-foot"><span class="quote-name">---- Theo Vance</span><span class="quote-close">&rdquo;</span></div>
  </div>
</section>

<footer class="site-footer">
  <div class="fcol" style="left:99px"><h4>Learn</h4><ul><li>Home</li><li>About Us</li><li>Services</li><li>Gallery</li><li>Contact</li></ul></div>
  <div class="fcol" style="left:329px"><h4>Featured</h4><ul><li>New Services</li><li>News &amp; Event</li><li>Services</li><li>Products</li><li>Partners</li></ul></div>
  <div class="fcol contact" style="left:550px"><h4>Contact</h4><ul><li><u>hello@brightfernstudies.example</u></li></ul></div>
  <div class="fcol news" style="left:805px"><h4>Newsletter Signup</h4>
    <p>Receive gentle notes, new course news and practice tips in your inbox, sent only now and then.</p>
    <div class="news-input">Email Addres<span><svg width="45" height="44" viewBox="0 0 45 44"><path fill="#fff" d="M15 22 L31 14 L27 31 L23 25 Z"/></svg></span></div>
    <div class="socials"><i></i><i></i><i></i></div>
  </div>
  <div class="footer-bar">
    <svg width="1200" height="65"><path fill="#0e0e0e" d="M600 0 L1200 0 L1200 65 L565 65 Z"/></svg>
    <span class="copy">Copyright © 2016 &nbsp;All Rights Reserved</span>
    <nav><span>Terms of Use</span><span>Legal disclaimer</span><span>Privacy Policy</span><span>Support</span><span>Sitemap</span></nav>
  </div>
</footer>

</body>
</html>
```